A parent Company needs a website as a leading diversified business in industrial Conglomerates in Af

Velkor Group is a private (Holding) limited liability company incorporated under the Companies Code, 1963 (Act 179) in November, 2013 to following the speedy growth in numbers of its current subsidiaries which has been founded several years ago with an emerging force to become one of the largest and a leading diversified business in industrial Conglomerates in Africa.
The Group which is 100% wholly owned indigenous Ghanaian Company focuses on provision of local, value-added products and services that meet the needs of the African population. The Group is headquartered in Accra, Ghana with interests across a range of sectors in Africa.
We are currently into Food & Beverage, Real Estate Development, Transportation, Health Care, Consumer Products Distribution, Agro Processing, Manufacturing, ICT, Exports & Import, and still counting.
In the next 3 years, we shall announce our ambitions to enter Ghana's largest Oil and Gas industry, playing a strategic role in the petroleum sector with strategic alliances, and help build Ghana's biggest and most important Energy sector in the country.
Inspired by billionaires Tom Prewitt, Harlan Voskel, and Emeka Ofodile, Velkor Group (Velkor Foundation) is committed to making a name for itself on the philanthropic circuit and has given away privately and still given to the cause to the needy in the society and some specific social causes in Ghana.
The company is managed by a 5 member board and a 2 member advisory experts who are non-board members.
The company has a vision, mission and it is guided by its core values.
We would like to see a designs that is very professional and looks corporate and can attract investors and partners. It must communicate financial safety and growth and must reflect our logo colors.

```html
<!DOCTYPE html>
<html lang="en">
<head>
<meta charset="utf-8">
<title>Velkor Group</title>
<link href="https://fonts.googleapis.com/css2?family=Open+Sans:wght@400;600;700&family=Questrial&display=swap" rel="stylesheet">
<style>
:root{
  --navy:#0d2a55;
  --hero-top:#123a70;
  --hero-mid:#1f4f8e;
  --blue:#0a5fc8;
  --blue-dark:#0c3f86;
  --orange:#f6931f;
  --orange-light:#fbb03b;
  --text:#555;
  --line:#d9d9d9;
  --footer:#1b1b1b;
  --footer-deep:#111;
  --footer-text:#7a7a7a;
  --white:#fff;
}
*{box-sizing:border-box;margin:0;padding:0}
html,body{width:717px;height:1200px;overflow:hidden;background:var(--white)}
body{position:relative;font-family:"Questrial",sans-serif;color:var(--text)}
.abs{position:absolute}

/* hero */
.hero{left:0;top:0;width:717px;height:334px;
  background:radial-gradient(ellipse at 45% 45%,#2c5d9c 0%,var(--hero-mid) 40%,var(--hero-top) 100%)}
.hero-band{left:0;top:0;width:717px;height:5px;background:var(--navy)}
.phone-tab{left:541px;top:4px;width:109px;height:21px;background:var(--navy);border-radius:0 0 4px 4px;
  color:var(--white);font:400 13px "Open Sans",sans-serif;display:flex;align-items:center;justify-content:center;gap:6px}
.brand{left:60px;top:18px;width:90px;text-align:center;color:var(--white)}
.brand-dot{width:22px;height:22px;border-radius:50%;background:#6fb6ee;margin:0 auto 6px}
.brand-name{font:600 12px "Open Sans",sans-serif}
.nav{top:42px}
.nav a{position:absolute;top:0;height:19px;background:var(--navy);color:var(--white);text-decoration:none;
  font:400 10px "Open Sans",sans-serif;display:flex;align-items:center;justify-content:center;border-radius:2px}
.hero-title{left:0;width:717px;top:124px;text-align:center;color:var(--white);font:600 21px "Open Sans",sans-serif}
.hero-text{left:118px;width:481px;top:172px;text-align:center;color:var(--white);font:400 14px/16px "Open Sans",sans-serif}
.cta{left:274px;top:250px;width:172px;height:34px;border-radius:17px;
  background:linear-gradient(var(--orange-light),var(--orange));box-shadow:0 3px 0 #c86d10;
  color:var(--white);font:700 10.5px "Open Sans",sans-serif;display:flex;align-items:center;justify-content:center}

/* sectors */
.sector-band{left:0;top:334px;width:717px;height:101px;background:linear-gradient(#fff,#ececec);border-bottom:1px solid #cfcfcf}
.sector{width:110px}
.sector-icon{position:absolute;top:34px;left:0;width:110px;height:42px}
.sector-tab{position:absolute;top:81px;left:0;width:110px;height:54px}
.sector-label{position:absolute;top:101px;left:0;width:110px;height:33px;color:var(--white);
  font:400 10px "Open Sans",sans-serif;display:flex;align-items:center;justify-content:center;text-align:center}
.sector-ribbon{position:absolute;top:143px;left:0;width:110px;height:16px}
.sector-ribbon span{position:absolute;inset:0;display:flex;align-items:center;justify-content:center;color:var(--white);font:400 8.5px "Open Sans",sans-serif}
.sector-copy{position:absolute;top:170px;left:0;width:112px;font-size:8.2px;line-height:12px;color:var(--text)}

/* main */
.rule{height:1px;background:linear-gradient(90deg,transparent,var(--line),transparent)}
.welcome{left:74px;top:616px;font:400 20px "Open Sans",sans-serif;color:#333}
.welcome b{color:var(--blue);font-weight:600}
.body-copy{left:73px;width:388px;font-size:8.2px;line-height:9.8px;color:var(--text)}
.body-copy p{margin-bottom:9px}
.body-copy strong{color:var(--blue-dark);font-weight:700}
.about-title{left:73px;top:842px;font:600 16px "Open Sans",sans-serif;color:#333}

/* access form */
.access{left:479px;top:628px;width:150px;height:200px;background:var(--blue-dark);border-radius:2px}
.access-tab{left:486px;top:618px;width:136px;height:20px;background:linear-gradient(#fff,#e6e6e6);border:1px solid #c9c9c9;
  display:flex;align-items:center;gap:8px;padding-left:8px;font:400 10.5px "Open Sans",sans-serif;color:var(--blue-dark)}
.access-tab i{width:11px;height:11px;border-radius:50%;background:#4aa3e0;display:block}
.field{left:486px;width:133px;height:15px;background:var(--white);border:1px solid #b8c4d6;font-size:7px;color:#777;padding:3px 5px}
.send{left:486px;top:804px;width:69px;height:18px;background:linear-gradient(var(--orange-light),var(--orange));
  color:var(--white);font:700 10px "Open Sans",sans-serif;display:flex;align-items:center;justify-content:center}
.resize{left:597px;top:804px;width:21px;height:16px;background:var(--white)}
.customers-title{left:479px;width:150px;top:841px;text-align:center;font:400 11.5px "Open Sans",sans-serif;color:#333}
.customer{left:479px;width:151px;height:49px;border:1px solid #cfcfcf;background:var(--white);display:flex;align-items:center;justify-content:center}
.customer div{width:90px;height:22px;border-radius:3px}

/* footer */
.footer{left:0;top:992px;width:717px;height:174px;background:var(--footer)}
.footer-bar{left:0;top:1166px;width:717px;height:34px;background:var(--footer-deep)}
.foot-title{font:400 11px "Open Sans",sans-serif;color:#ddd;padding-bottom:3px;border-bottom:1px solid #555}
.blog-item{left:73px;width:165px;font-size:7.5px;line-height:9px;color:#8a8a8a;display:flex;gap:5px;padding-bottom:5px;border-bottom:1px solid #2e2e2e}
.blog-item i{flex:none;width:7px;height:8px;border:1px solid #aaa;margin-top:1px}
.service{left:305px;font-size:7.5px;color:var(--footer-text)}
.service.active{color:var(--white)}
.social{top:1142px;width:17px;height:17px;border-radius:2px}
.contact{left:510px;font-size:7.5px;line-height:8.5px;color:var(--footer-text);display:flex;gap:7px}
.contact svg{flex:none;margin-top:1px}
.foot-brand{left:524px;top:1133px;width:106px;text-align:center;font:600 11px "Open Sans",sans-serif;color:var(--white)}
.bottom-link{top:1179px;font-size:7.5px;color:var(--footer-text)}
.copyright{right:67px;top:1179px;font-size:7.5px;color:#666}
</style>
</head>
<body>

<!-- hero -->
<section class="abs hero" role="img" aria-label="Blurred blue city skyline backdrop behind the hero message"></section>
<div class="abs hero-band"></div>
<div class="abs phone-tab">
  <svg width="7" height="11" viewBox="0 0 7 11"><rect x=".5" y=".5" width="6" height="10" rx="1" fill="none" stroke="#fff"/><circle cx="3.5" cy="8.7" r=".7" fill="#fff"/></svg>
  (07) 418 2290
</div>
<div class="abs brand"><div class="brand-dot"></div><div class="brand-name">Velkor Group</div></div>
<nav class="abs nav">
  <a style="left:291px;width:35px">Home</a>
  <a style="left:334px;width:31px">Food</a>
  <a style="left:373px;width:117px">Real Estate Development</a>
  <a style="left:496px;width:74px">Transportation</a>
  <a style="left:578px;width:73px">Manufacturing</a>
</nav>
<h1 class="abs hero-title">VELKOR GROUP</h1>
<p class="abs hero-text">A 100% Ghanaian holding company growing into one of Africa’s leading diversified industrial conglomerates, delivering local, value-added products and services across the continent.</p>
<div class="abs cta">VIEW OUR FULL PORTFOLIO</div>
<svg class="abs" style="left:455px;top:236px" width="100" height="42" viewBox="0 0 100 42">
  <path d="M95 3 C80 22 50 34 6 38" fill="none" stroke="#fff" stroke-width="1.6"/>
  <path d="M12 33 L4 38 L12 42" fill="none" stroke="#fff" stroke-width="1.6"/>
</svg>

<!-- sectors -->
<div class="abs sector-band"></div>

<div class="abs sector" style="left:66px;top:334px">
  <svg class="sector-icon" viewBox="0 0 110 42">
    <g fill="#1a1a1a">
      <rect x="43" y="0" width="2" height="14"/><rect x="47" y="0" width="2" height="14"/><rect x="51" y="0" width="2" height="14"/>
      <path d="M42 13 h12 v3 q-2 3 -4 3 v22 h-4 v-22 q-2 0 -4 -3z"/>
      <path d="M60 0 q8 4 6 20 h-2 v21 h-4z"/>
    </g>
  </svg>
  <svg class="sector-tab" viewBox="0 0 110 54"><path d="M34 20 L55 0 L76 20 H110 V54 H0 V20Z" fill="var(--blue)"/></svg>
  <div class="sector-label">FOOD</div>
  <svg class="sector-ribbon" viewBox="0 0 110 16"><path d="M8 0 H102 L110 8 L102 16 H8 L0 8Z" fill="#1e1e1e"/></svg>
  <div class="sector-ribbon"><span>We love Food</span></div>
  <p class="sector-copy">Food &amp; beverage and agro processing that turn local harvests into quality products for African homes.</p>
</div>

<div class="abs sector" style="left:225px;top:334px">
  <svg class="sector-icon" viewBox="0 0 110 42">
    <g fill="#1a1a1a">
      <path d="M55 0 L72 13 H68 V20 H42 V13 H38Z"/>
      <rect x="37" y="19" width="36" height="22"/>
      <rect x="41" y="23" width="28" height="14" fill="#fff"/>
      <circle cx="55" cy="30" r="5"/>
    </g>
  </svg>
  <svg class="sector-tab" viewBox="0 0 110 54"><path d="M34 20 L55 0 L76 20 H110 V54 H0 V20Z" fill="var(--blue)"/></svg>
  <div class="sector-label">ESTATE DEVELOPMENT</div>
  <svg class="sector-ribbon" viewBox="0 0 110 16"><path d="M8 0 H102 L110 8 L102 16 H8 L0 8Z" fill="#1e1e1e"/></svg>
  <div class="sector-ribbon"><span>We love Development</span></div>
  <p class="sector-copy">Residential and commercial property built to last, creating secure, growing assets for our partners.</p>
</div>

<div class="abs sector" style="left:383px;top:334px">
  <svg class="sector-icon" viewBox="0 0 110 42">
    <g fill="#1a1a1a">
      <rect x="32" y="8" width="30" height="26"/>
      <path d="M64 16 H74 L80 25 V34 H64Z"/>
      <circle cx="42" cy="36" r="5"/><circle cx="72" cy="36" r="5"/>
    </g>
    <circle cx="42" cy="36" r="2" fill="#fff"/><circle cx="72" cy="36" r="2" fill="#fff"/>
  </svg>
  <svg class="sector-tab" viewBox="0 0 110 54"><path d="M34 20 L55 0 L76 20 H110 V54 H0 V20Z" fill="var(--blue)"/></svg>
  <div class="sector-label">TRANSPORTATION</div>
  <svg class="sector-ribbon" viewBox="0 0 110 16"><path d="M8 0 H102 L110 8 L102 16 H8 L0 8Z" fill="#1e1e1e"/></svg>
  <div class="sector-ribbon"><span>We love Transportation</span></div>
  <p class="sector-copy">Reliable haulage and distribution moving consumer products, exports and imports across the region.</p>
</div>

<div class="abs sector" style="left:540px;top:334px">
  <svg class="sector-icon" viewBox="0 0 110 42">
    <g fill="#1a1a1a">
      <rect x="37" y="2" width="5" height="20"/>
      <path d="M36 41 V20 L46 14 V20 L56 14 V20 L66 14 V20 L75 14 V41Z"/>
    </g>
    <g fill="#fff"><rect x="41" y="26" width="4" height="4"/><rect x="49" y="26" width="4" height="4"/><rect x="57" y="26" width="4" height="4"/><rect x="65" y="26" width="4" height="4"/></g>
  </svg>
  <svg class="sector-tab" viewBox="0 0 110 54"><path d="M34 20 L55 0 L76 20 H110 V54 H0 V20Z" fill="var(--blue)"/></svg>
  <div class="sector-label">MANUFACTURING</div>
  <svg class="sector-ribbon" viewBox="0 0 110 16"><path d="M8 0 H102 L110 8 L102 16 H8 L0 8Z" fill="#1e1e1e"/></svg>
  <div class="sector-ribbon"><span>We love Manufacturing</span></div>
  <p class="sector-copy">Local production plants making value-added goods that meet the needs of the African population.</p>
</div>

<!-- welcome -->
<div class="abs rule" style="left:70px;top:596px;width:570px"></div>
<h2 class="abs welcome">Welcome to <b>VELKOR GROUP</b></h2>
<div class="abs body-copy" style="top:660px">
  <p>Velkor Group is a private (holding) limited liability company incorporated under the Companies Code, 1963 (Act 179) in November 2013, following the speedy growth of its subsidiaries. The Group is 100% wholly owned, indigenous and Ghanaian, headquartered in Accra, with interests in Food &amp; Beverage, Real Estate Development, Transportation, Health Care, Consumer Products Distribution, Agro Processing, Manufacturing, ICT, and Exports &amp; Imports.</p>
  <p>Within the next three years we shall announce our entry into Ghana’s Oil and Gas industry, playing a strategic role in the petroleum sector through strategic alliances.</p>
  <p>To find out more about investment and partnership opportunities, browse our About Us and Portfolio or call our investor relations team on <strong>07 418 2290</strong>. We work hard to ensure every partnership is built on financial safety, transparency and long-term growth for our shareholders and the communities we serve.</p>
</div>
<div class="abs" style="left:77px;top:821px;width:388px;height:1px;background:var(--line)"></div>
<h2 class="abs about-title">ABOUT US</h2>
<div class="abs body-copy" style="top:868px">
  <p>Velkor Group is managed by a five-member board supported by two advisory experts who are non-board members. The company is guided by a clear vision, a clear mission and its core values of integrity, excellence and responsible growth across every subsidiary.</p>
  <p>Inspired by Tom Prewitt, Harlan Voskel and Emeka Ofodile, the Velkor Foundation gives to the needy and to specific social causes in Ghana.</p>
  <p>Our ambition is to help build Ghana’s biggest and most important Energy sector, and to become one of the largest diversified industrial conglomerates in Africa, creating jobs, value and lasting returns for investors and partners.</p>
</div>

<!-- private access -->
<div class="abs access"></div>
<div class="abs access-tab"><i></i>Private Access</div>
<div class="abs field" style="top:648px">Name</div>
<div class="abs field" style="top:667px">Company</div>
<div class="abs field" style="top:686px">Phone Number</div>
<div class="abs field" style="top:705px">Email Address</div>
<div class="abs field" style="top:723px">Website Address</div>
<div class="abs field" style="top:742px;height:56px">Enter your message here</div>
<div class="abs send">SEND</div>
<div class="abs resize"></div>

<h3 class="abs customers-title">A Few Our Customer</h3>
<div class="abs customer" style="top:863px"><div style="background:#29a9e1"></div></div>
<div class="abs customer" style="top:917px"><div style="background:#2f9a3e"></div></div>

<!-- footer -->
<footer class="abs footer"></footer>
<div class="abs footer-bar"></div>

<div class="abs foot-title" style="left:73px;top:1004px;width:165px">Latest Blog Entries</div>
<div class="abs blog-item" style="top:1033px"><i></i><span>Velkor Group Expands Agro Processing in Ghana</span></div>
<div class="abs blog-item" style="top:1065px"><i></i><span>Our Roadmap Into Oil and Gas by 2017</span></div>
<div class="abs blog-item" style="top:1096px"><i></i><span>Velkor Foundation Community Giving</span></div>

<div class="abs foot-title" style="left:306px;top:1004px;width:134px">Our Services</div>
<div class="abs service active" style="top:1032px">Home</div>
<div class="abs service" style="top:1047px">food</div>
<div class="abs service" style="top:1062px">Real Estate Development</div>
<div class="abs service" style="top:1077px">Transportation</div>
<div class="abs service" style="top:1092px">Manufacturing</div>

<div class="abs foot-title" style="left:306px;top:1116px;width:85px">Follow Us</div>
<div class="abs social" style="left:306px;background:#3b5b98"></div>
<div class="abs social" style="left:333px;background:#3fa9e0"></div>
<div class="abs social" style="left:360px;background:#1b75b3"></div>

<div class="abs foot-title" style="left:510px;top:1004px;width:134px">Quick Contact</div>
<div class="abs contact" style="top:1033px">
  <svg width="7" height="7" viewBox="0 0 7 7"><path d="M3.5 0 L7 3 H6 V7 H1 V3 H0Z" fill="#ccc"/></svg>
  <span>Plot 14 Osu Ridge Lane<br>Ridge<br>Accra<br>Ghana, GA-018</span>
</div>
<div class="abs contact" style="top:1077px">
  <svg width="8" height="6" viewBox="0 0 8 6"><rect x=".5" y=".5" width="7" height="5" fill="none" stroke="#ccc"/><path d="M.5 .5 L4 3.5 L7.5 .5" fill="none" stroke="#ccc"/></svg>
  <span>info@velkorgroup.com.gh</span>
</div>
<div class="abs contact" style="top:1095px">
  <svg width="6" height="10" viewBox="0 0 6 10"><rect x=".5" y=".5" width="5" height="9" rx="1" fill="none" stroke="#ccc"/></svg>
  <span>07 418 2290 or<br>0800 00 61 28</span>
</div>
<div class="abs foot-brand">VELKOR GROUP</div>

<div class="abs bottom-link" style="left:68px">Home</div>
<div class="abs bottom-link" style="left:102px">Food</div>
<div class="abs bottom-link" style="left:134px">Real Estate Development</div>
<div class="abs bottom-link" style="left:232px">Transportation</div>
<div class="abs bottom-link" style="left:298px">Manufacturing</div>
<div class="abs copyright">Copyright 2014 © Velkor Group All Rights Reserved</div>

</body>
</html>
```